Verlindo Magician

I want the business card for my business to give to people who watch that later I will be employed to show magic here is my website http://www.verlindoillusions.example/I want the interesting design , i am very opened for formal and informal, I watch a lot of design so don't stick to the common shape and form but i hope it can also be produced the thing to write on will be the same as in picture that i will upload , i also will upload the logo for you that so can be easy to useDenis CostilleMagicianMAGICIAN VERLINDO 17 rue des Tilleuls - 25000 BESANÇON contact@verlindoillusions.example tel. 0381 946 157 tel. 0674 219 503

```html
<!DOCTYPE html>
<html lang="fr">
<head>
<meta charset="utf-8">
<title>Verlindo Magician — Business Card</title>
<link rel="stylesheet" href="https://fonts.googleapis.com/css2?family=Open+Sans:wght@300;400;700&display=swap">
<style>
  :root {
    --backdrop: #d6d6d6;
    --card-white: #ffffff;
    --card-black: #050505;
    --ink: #111111;
    --accent-red: #e8392a;
    --divider: #c9c9c9;
    --pattern-dark: #141414;
    --figure-dark: #1a1a1a;
    --figure-mid: #4a4a4a;
  }
  * { box-sizing: border-box; margin: 0; padding: 0; }
  html, body { width: 1200px; height: 782px; overflow: hidden; }
  body {
    background: var(--backdrop);
    font-family: "Open Sans", Arial, sans-serif;
    position: relative;
  }
  .card {
    position: absolute;
    width: 560px;
    height: 320px;
    box-shadow: 0 6px 18px rgba(0,0,0,.25);
    overflow: hidden;
  }

  /* Back side */
  .card-back { left: 590px; top: 60px; background: var(--card-black); }
  .card-back .back-texture {
    position: absolute; inset: 0;
    background: linear-gradient(135deg, var(--pattern-dark), var(--card-black));
  }
  .card-back .back-name {
    position: absolute; left: 0; right: 0; top: 258px;
    text-align: center;
    color: var(--card-white);
    font-weight: 300;
    font-size: 22px;
    letter-spacing: 2px;
  }

  /* Front side */
  .card-front { left: 50px; top: 402px; background: var(--card-white); }
  .portrait {
    position: absolute; left: 82px; top: 28px;
    width: 150px; height: 160px;
    background: linear-gradient(180deg, var(--figure-mid), var(--figure-dark));
    border-radius: 40px 40px 6px 6px;
  }
  .front-name {
    position: absolute; left: 40px; top: 196px; width: 240px;
    text-align: center;
    color: var(--ink);
    font-weight: 300;
    font-size: 30px;
    letter-spacing: 2px;
  }
  .divider {
    position: absolute; left: 290px; top: 70px;
    width: 1px; height: 180px;
    background: var(--divider);
  }
  .details { position: absolute; left: 312px; top: 72px; color: var(--ink); }
  .person-name { font-weight: 700; font-size: 19px; letter-spacing: .5px; line-height: 1.1; }
  .person-role { color: var(--accent-red); font-size: 13px; margin-bottom: 4px; }
  .contact-list { list-style: none; font-size: 13px; line-height: 17px; }
  .contact-list li { display: flex; align-items: center; gap: 6px; }
  .contact-list svg { width: 11px; height: 11px; fill: var(--ink); flex: none; }
  .company { font-weight: 700; font-size: 13px; margin-top: 3px; line-height: 16px; }
  .address { font-size: 13px; line-height: 16px; }
  .bands { position: absolute; left: 0; bottom: 0; width: 560px; height: 60px; }
</style>
</head>
<body>

  <section class="card card-back" aria-label="Card back">
    <div class="back-texture" role="img" aria-label="Dark repeating name pattern background"></div>
    <div class="back-name">VERLINDO</div>
  </section>

  <section class="card card-front" aria-label="Card front">
    <div class="portrait" role="img" aria-label="Black and white illustration of the magician holding a playing card"></div>
    <div class="front-name">VERLINDO</div>
    <div class="divider"></div>

    <div class="details">
      <div class="person-name">MARC RAVOULET</div>
      <div class="person-role">Magician</div>
      <ul class="contact-list">
        <li><svg viewBox="0 0 12 12"><path d="M1 4c0-2 2-3 5-3s5 1 5 3v1H8V4H4v1H1zM2 6h8l1 5H1z"/></svg>0381 946 157</li>
        <li><svg viewBox="0 0 12 12"><path d="M1 4c0-2 2-3 5-3s5 1 5 3v1H8V4H4v1H1zM2 6h8l1 5H1z"/></svg>0674 219 503</li>
        <li><svg viewBox="0 0 12 12"><path d="M0 2h12v8H0zM1 3l5 4 5-4v-.2H1z" fill-rule="evenodd"/></svg>contact@verlindoillusions.example</li>
        <li><svg viewBox="0 0 12 12"><circle cx="6" cy="6" r="5.5"/><path d="M1 6h10M6 .5c-2 2.5-2 8.5 0 11M6 .5c2 2.5 2 8.5 0 11" stroke="#fff" stroke-width=".8" fill="none"/></svg>www.verlindoillusions.example</li>
      </ul>
      <div class="company">MAGICIAN VERLINDO</div>
      <div class="address">17 rue des Tilleuls - 25000<br>BESANÇON</div>
    </div>

    <svg class="bands" viewBox="0 0 560 60" aria-hidden="true">
      <polygon points="0,10 258,10 248,26 0,26" fill="var(--accent-red)"/>
      <polygon points="262,20 560,20 560,60 240,60" fill="var(--card-black)"/>
    </svg>
  </section>

</body>
</html>
```